Workshop PPT Update for AI Transformation Sessions

Our strategic consulting firm runs strategy workshops using slides as workshop exercises. These slides are used to communicate to the participants in advance, run the workshops and produce the final deliverable.

It is time for a design "upgrade". We'd like them to be more engaging, hipper and more interesting. These slides are utilitarian, so clean and usable is good. I have attached the example of what we have today. I have also attached an example of another company's slides that I like.

We can't rip off their design nor can we go away 100% from what we have. But I think it is possible to "update" our look to something closer to their look. Grey colors are fine with some color pop.

Slide styles needed are - 1) Cover Page, 2) Instructions Page, 3) Bullet list 4) Worksheet (place for participants to add content 5) Table, 6) Two column.

```html
<!DOCTYPE html>
<html lang="en">
<head>
<meta charset="utf-8">
<title>NorthPath – Kickoff &amp; Discovery Workshop Deck</title>
<link rel="stylesheet" href="https://fonts.googleapis.com/css2?family=Open+Sans:ital,wght@0,400;0,600;0,700;1,400&display=swap">
<style>
:root{
  --brick:#a34a3f;
  --brick-soft:#f4e4e1;
  --blush:#e2c5c1;
  --charcoal:#2b2b2d;
  --slate:#4a4a4f;
  --grey-panel:#f2f1ef;
  --grey-line:#d9d7d4;
  --ink:#1a1a1a;
  --muted:#5a5a5e;
  --page:#000;
  --paper:#fff;
}
*{box-sizing:border-box;margin:0;padding:0}
html,body{width:1200px;height:4013px;overflow:hidden;background:var(--page)}
body{position:relative;font-family:"Open Sans",Arial,sans-serif;color:var(--ink)}
.slide{position:absolute;left:72px;width:1056px;height:592px;background:var(--paper);overflow:hidden}
.abs{position:absolute}
.footer-copy{position:absolute;left:53px;top:561px;font-size:14px;color:var(--muted);line-height:20px}
.footer-rule{position:absolute;left:390px;top:571px;width:504px;height:2px;background:var(--brick)}
.brand{position:absolute;right:53px;top:558px;font-size:20px;font-weight:600;color:var(--brick);line-height:24px}
.slide-title{position:absolute;left:50px;font-size:36px;font-weight:700;line-height:44px;color:var(--charcoal);letter-spacing:-.3px}
.slide-title .accent{color:var(--brick)}
.title-bar{position:absolute;left:52px;width:56px;height:4px;border-radius:2px;background:var(--brick)}

/* cover */
.cover{top:61px}
.cover-band{left:757px;top:0;width:299px;height:592px;background:var(--blush)}
.cover-photo{left:53px;top:34px;width:950px;height:471px;border-radius:14px;background:linear-gradient(100deg,#3a3430 0%,#6b5a4c 55%,#c8b29a 80%,#8a7766 100%)}
.cover-shade{left:53px;top:61px;width:676px;height:444px;border-radius:0 0 0 14px;background:rgba(38,38,40,.82)}
.cover-accent{left:109px;top:185px;width:48px;height:4px;border-radius:2px;background:var(--brick)}
.cover-brand{left:109px;top:200px;font-size:40px;color:#fff;line-height:46px}
.cover-title{left:109px;top:265px;font-size:46px;font-weight:700;color:#fff;line-height:54px;letter-spacing:.5px}
.cover-sub{left:110px;top:345px;font-size:19px;color:#fff;letter-spacing:.6px}
.cover .footer-rule{left:395px;width:608px}

/* stop */
.stop{top:721px}
.stop-panel{left:0;top:0;width:437px;height:592px;background:var(--grey-panel)}
.stop-head{left:53px;top:52px;font-size:33px;font-weight:700;line-height:40px;color:var(--brick)}
.stop-photo{left:53px;top:125px;width:384px;height:380px;border-radius:14px 0 0 14px;background:linear-gradient(160deg,#e9e7e3 0%,#b8b2aa 45%,#5c5650 100%)}
.stop-lead{left:481px;top:58px;width:520px;font-size:22px;font-weight:600;line-height:36px;color:var(--charcoal)}
.need-list{left:481px;top:152px;list-style:none;width:540px}
.need-list li{position:relative;height:90px;padding-left:87px;font-size:17px;line-height:36px;display:flex;align-items:center}
.need-icon{position:absolute;left:5px;top:11px;width:68px;height:68px;border-radius:50%;display:flex;align-items:center;justify-content:center}
.need-icon.red{background:var(--brick)}
.need-icon.dark{background:var(--charcoal)}

/* plan table */
.plan{top:1380px}
.plan-table{position:absolute;left:53px;top:107px;width:951px;border-collapse:separate;border-spacing:0;font-size:13px;text-align:center;border:1px solid var(--grey-line);border-radius:12px;overflow:hidden}
.plan-table th{background:var(--charcoal);color:#fff;font-weight:600;font-size:16px;height:45px;border-right:1px solid #444}
.plan-table th:first-child{border-left:6px solid var(--brick)}
.plan-table th:last-child{border-right:0}
.plan-table td{border-top:1px solid var(--grey-line);border-right:1px solid var(--grey-line);line-height:26px}
.plan-table td:last-child{border-right:0}
.plan-table tr.alt td{background:var(--grey-panel)}
.plan-table td.lvl{font-size:16px;font-weight:600;color:var(--brick)}
.plan-table em{font-style:italic}

/* workshop */
.workshop{top:2041px}
.flow-sub{left:56px;top:76px;font-size:23px;font-weight:600;color:var(--charcoal)}
.flow-line{left:71px;top:145px;width:2px;height:343px;background:var(--grey-line)}
.flow-step{position:absolute;left:53px;width:600px}
.flow-num{position:absolute;left:0;top:0;width:38px;height:38px;border-radius:50%;background:var(--brick);color:#fff;font-size:16px;font-weight:600;display:flex;align-items:center;justify-content:center}
.flow-name{position:absolute;left:54px;top:-8px;font-size:17px;font-weight:600;white-space:nowrap;color:var(--charcoal)}
.flow-note{position:absolute;left:54px;top:20px;font-size:11px;color:var(--muted);white-space:nowrap}
.prep-card{left:648px;top:67px;width:332px;height:411px;background:var(--charcoal);border-radius:18px;color:#fff;overflow:hidden}
.prep-card::before{content:"";position:absolute;left:0;top:0;width:100%;height:6px;background:var(--brick)}
.prep-meta{position:absolute;left:44px;top:48px;font-size:16px;font-weight:600;line-height:27px}
.prep-title{position:absolute;left:46px;top:116px;font-size:16px;font-weight:600}
.prep-list{position:absolute;left:46px;top:158px;list-style:none}
.prep-list li{position:relative;padding-left:62px;height:60px;font-size:14px;line-height:44px}
.prep-dot{position:absolute;left:0;top:0;width:44px;height:44px;border-radius:50%;background:var(--brick);display:flex;align-items:center;justify-content:center}

/* guiding principles creation */
.create{top:2700px}
.material-card{left:53px;top:112px;width:327px;height:377px;background:var(--brick);border-radius:18px;color:#fff}
.material-card h3{position:absolute;left:31px;font-size:20px;font-weight:600}
.material-list{position:absolute;left:31px;top:78px;list-style:none}
.material-list li{position:relative;padding-left:25px;font-size:13px;line-height:33px}
.material-list li::before{content:"";position:absolute;left:0;top:12px;width:10px;height:10px;border-radius:50%;background:#fff}
.material-small{position:absolute;left:31px;font-size:13px}
.purpose-box{left:427px;top:104px;width:577px;height:80px;background:var(--grey-panel);border-left:5px solid var(--brick);border-radius:0 12px 12px 0;padding:7px 10px;font-size:16px;line-height:33px}
.purpose-box b{color:var(--brick);font-weight:600;font-size:19px}
.instr-head{left:445px;top:196px;font-size:20px;font-weight:600;color:var(--brick)}
.instr-list{left:445px;top:240px;list-style:none;width:560px}
.instr-list li{position:relative;padding-left:32px;font-size:16px;font-weight:600;line-height:33px;color:var(--charcoal)}
.instr-list li span.n{position:absolute;left:0;font-weight:600;color:var(--brick)}
.instr-list li small{display:block;font-size:13px;font-weight:400;line-height:22px;margin:6px 0;color:var(--muted)}

/* principles */
.principles{top:3361px}
.principles-sub{left:54px;top:86px;font-size:16px;color:var(--muted)}
.principle{position:absolute;width:283px;height:181px;background:var(--paper);border:1px solid var(--grey-line);border-top:5px solid var(--brick);border-radius:14px;text-align:center;padding:24px 18px 0;box-shadow:0 6px 14px rgba(0,0,0,.08)}
.principle.dark{border-top-color:var(--charcoal);background:var(--grey-panel)}
.principle h4{font-size:17px;font-weight:600;color:var(--brick);margin-bottom:10px}
.principle.dark h4{color:var(--charcoal)}
.principle p{font-size:13px;line-height:26px;color:var(--ink)}
</style>
</head>
<body>

<section class="slide cover">
  <div class="abs cover-band"></div>
  <div class="abs cover-photo" role="img" aria-label="Photo of a smiling professional reviewing documents and a tablet in a meeting"></div>
  <div class="abs cover-shade"></div>
  <div class="abs cover-accent"></div>
  <div class="abs cover-brand">NorthPath</div>
  <h1 class="abs cover-title">KICKOFF &amp; DISCOVERY</h1>
  <p class="abs cover-sub">SIZING &amp; SCOPING AI TRANSFORMATION</p>
  <p class="footer-copy">Copyrights@2024.NorthPath.All Rights Reserved</p>
  <div class="footer-rule"></div>
</section>

<section class="slide stop">
  <div class="abs stop-panel"></div>
  <h2 class="abs stop-head">STOP!!</h2>
  <div class="abs stop-photo" role="img" aria-label="Photo of a team meeting around a conference table with laptops"></div>
  <p class="abs stop-lead">All process need the following (regardless of doing which workshops being conducted):</p>
  <ul class="abs need-list">
    <li><span class="need-icon red"><svg width="34" height="34" viewBox="0 0 34 34" fill="none" stroke="#fff" stroke-width="2"><circle cx="17" cy="17" r="13"/><circle cx="17" cy="17" r="7"/><circle cx="17" cy="17" r="1.5" fill="#fff"/><path d="M17 17 L29 5"/></svg></span>Mission &amp; Vision</li>
    <li><span class="need-icon dark"><svg width="34" height="34" viewBox="0 0 34 34" fill="none" stroke="#fff" stroke-width="2"><circle cx="12" cy="12" r="7"/><circle cx="23" cy="23" r="7"/><path d="M12 9v6M9 12h6"/></svg></span>Strategic Goals &amp; 2024 OKRs (or priorities)</li>
    <li><span class="need-icon red"><svg width="34" height="34" viewBox="0 0 34 34" fill="none" stroke="#fff" stroke-width="2"><circle cx="17" cy="17" r="6"/><path d="M17 3v6M17 25v6M3 17h6M25 17h6M7 7l4 4M23 23l4 4M27 7l-4 4M11 23l-4 4"/></svg></span><span>AI Vision: How will AI enable you to &nbsp; multiply<br>your mission?</span></li>
    <li><span class="need-icon dark"><svg width="34" height="34" viewBox="0 0 34 34" fill="none" stroke="#fff" stroke-width="2"><rect x="8" y="5" width="18" height="24" rx="2"/><rect x="12" y="10" width="10" height="8"/><path d="M12 22h10M12 25h7"/></svg></span>AI Guiding Principles</li>
  </ul>
  <p class="footer-copy">Copyrights@2024.NorthPath.All Rights Reserved</p>
  <div class="footer-rule"></div>
  <div class="brand">NorthPath</div>
</section>

<section class="slide plan">
  <h2 class="slide-title" style="top:33px"><span class="accent">Plan</span> Structure</h2>
  <table class="plan-table">
    <thead>
      <tr><th colspan="2" style="width:185px">Level</th><th style="width:291px">Planing Element &amp; Definition</th><th style="width:209px">Accountability/Owner</th><th style="width:265px">Frequency of Modificantion</th></tr>
    </thead>
    <tbody>
      <tr style="height:81px"><td class="lvl" style="width:87px">1</td><td>What<br>(Overall)</td><td>Strategic Priorities</td><td>N/A</td><td>3+ Years</td></tr>
      <tr class="alt" style="height:78px"><td class="lvl">1.1</td><td>What<br>(this year)</td><td>Goals<br><em>Outcomes &amp; Strategies</em></td><td>Executive Leadership</td><td>1-3 Years</td></tr>
      <tr style="height:86px"><td class="lvl">1.1.1</td><td rowspan="2" style="background:#fff">How</td><td>Key Performance Indicators<br>and/or Initiatives</td><td></td><td>1 &nbsp;(W/qrtly targets)Year</td></tr>
      <tr class="alt" style="height:76px"><td class="lvl">1.1.1</td><td>Action Items</td><td></td><td>Quarterly/Monthly</td></tr>
    </tbody>
  </table>
  <p class="footer-copy">Copyrights@2024.NorthPath.All Rights Reserved</p>
  <div class="footer-rule"></div>
  <div class="brand">NorthPath</div>
</section>

<section class="slide workshop">
  <h2 class="slide-title" style="top:22px"><span class="accent">Workshop</span> Overview</h2>
  <h3 class="abs flow-sub">Workshop Flow</h3>
  <div class="abs flow-line"></div>
  <div class="flow-step" style="top:126px"><span class="flow-num">1</span><span class="flow-name">Confirm Company Direction</span><span class="flow-note">Recap organizational purpose, values, vision &amp; winning strategy.</span></div>
  <div class="flow-step" style="top:194px"><span class="flow-num">2</span><span class="flow-name">Develop AI Vision</span></div>
  <div class="flow-step" style="top:263px"><span class="flow-num">3</span><span class="flow-name">Develop AI Guiding Principles</span><span class="flow-note">Developed AI Guiding Principles, supporting policies to include approved tools.</span></div>
  <div class="flow-step" style="top:332px"><span class="flow-num">4</span><span class="flow-name">Agree on a Governance Approach</span><span class="flow-note">Agreed upon governance approach, structure, &amp; executive champion.</span></div>
  <div class="flow-step" style="top:400px"><span class="flow-num">5</span><span class="flow-name">Agree on a Training &amp; Learning Approach</span><span class="flow-note">Set approach to training &amp; continuous learning.</span></div>
  <div class="flow-step" style="top:469px"><span class="flow-num">6</span><span class="flow-name">Determine Rollout &amp; Communication</span><span class="flow-note">Organizational rollout &amp; continuous communication.</span></div>
  <div class="abs prep-card">
    <p class="prep-meta">Participants: Execs<br>Duration: &nbsp;2 hrs.</p>
    <p class="prep-title">Prep Work:</p>
    <ul class="prep-list">
      <li><span class="prep-dot"><svg width="24" height="24" viewBox="0 0 24 24" fill="none" stroke="#fff" stroke-width="1.6"><circle cx="12" cy="12" r="9"/><circle cx="12" cy="12" r="4"/><path d="M12 12l8-8"/></svg></span>Org Strategy</li>
      <li><span class="prep-dot"><svg width="24" height="24" viewBox="0 0 24 24" fill="none" stroke="#fff" stroke-width="1.6"><path d="M4 20h16M6 20v-5M11 20v-8M16 20v-11M5 11l6-5 4 3 5-5"/></svg></span>2023 Goal Performance</li>
      <li><span class="prep-dot"><svg width="24" height="24" viewBox="0 0 24 24" fill="none" stroke="#fff" stroke-width="1.6"><rect x="5" y="3" width="14" height="18" rx="1.5"/><path d="M8 8h8M8 12h8M8 16h5"/></svg></span>Existing policies</li>
      <li><span class="prep-dot"><svg width="24" height="24" viewBox="0 0 24 24" fill="none" stroke="#fff" stroke-width="1.6"><path d="M4 5h11v8H9l-4 3v-3H4z"/><circle cx="17" cy="15" r="4"/><path d="M17 13.5v1.5"/></svg></span>Pre-thinking questions</li>
    </ul>
  </div>
  <p class="footer-copy">Copyrights@2024.NorthPath.All Rights Reserved</p>
  <div class="footer-rule"></div>
  <div class="brand">NorthPath</div>
</section>

<section class="slide create">
  <h2 class="slide-title" style="top:28px"><span class="accent">Creating your AI</span> Guiding Principles</h2>
  <div class="abs material-card">
    <h3 style="top:26px">Your Existing Material</h3>
    <ul class="material-list">
      <li>Company Values</li>
      <li>Current Policies (GDPR, CCPA, etc.)</li>
      <li>Legal Guidance</li>
      <li>OTHER</li>
    </ul>
    <h3 style="top:222px">Examples for Inspiration</h3>
    <p class="material-small" style="top:262px">See next slides</p>
    <h3 style="top:288px">AssistantAI Prompts</h3>
    <p class="material-small" style="top:332px">HERE</p>
  </div>
  <div class="abs purpose-box"><b>Purpose:</b>&nbsp; To create behavioral statements that everyone is expected to adhere to.</div>
  <h3 class="abs instr-head">Instructions:</h3>
  <ol class="abs instr-list">
    <li><span class="n">1.</span>Create the Outline.<small>Determine the topics that need a principle.</small></li>
    <li><span class="n">2.</span>Audit the Outline.<small>Look at the current policies to determine if all topics are covered.</small></li>
    <li><span class="n">3.</span>Draft the Guiding Principles.</li>
    <li><span class="n">4.</span>Determine which GPs need detailed policies.</li>
    <li><span class="n">5.</span>Determine which AI Tools support the GPs.</li>
    <li><span class="n">6.</span>Finalize via a legal and executive review.</li>
  </ol>
  <p class="footer-copy">Copyrights@2024.NorthPath.All Rights Reserved</p>
  <div class="footer-rule"></div>
  <div class="brand">NorthPath</div>
</section>

<section class="slide principles">
  <h2 class="slide-title" style="top:28px"><span class="accent">AI Guiding</span> Principles</h2>
  <p class="abs principles-sub">What guides our decision-making and approach?</p>
  <div class="principle" style="left:55px;top:132px"><h4>Principle #1</h4><p>Complete perspective from Executives, Directors, Managers &amp; Staff. Conduct competitive analysis and customer research (optional).</p></div>
  <div class="principle dark" style="left:385px;top:132px"><h4>Principle #2</h4><p>Complete perspective from Executives, Directors, Managers &amp; Staff. Conduct competitive analysis and customer research (optional)</p></div>
  <div class="principle" style="left:715px;top:132px"><h4>Principle #3</h4><p>Complete perspective from Executives, Directors, Managers &amp; Staff. Conduct competitive analysis and customer research (optional).</p></div>
  <div class="principle dark" style="left:220px;top:335px"><h4>Principle #4</h4><p>Complete perspective from Executives, Directors, Managers &amp; Staff. Conduct competitive analysis and customer research (optional).</p></div>
  <div class="principle" style="left:550px;top:335px"><h4>Principle #5</h4><p>Complete perspective from Executives, Directors, Managers &amp; Staff. Conduct competitive analysis and customer research (optional).</p></div>
  <p class="footer-copy">Copyrights@2024.NorthPath.All Rights Reserved</p>
  <div class="footer-rule"></div>
  <div class="brand">NorthPath</div>
</section>

</body>
</html>
```